Moravel Aesthetic Doctor

I require an elegant, luxurious looking business card for my aesthetic business. I am a doctor and that will set me aside from competitors. I am planning to provide home and spa based treatments to clients with high expectations. I have attached my logo.

```html
<!DOCTYPE html>
<html lang="en">
<head>
<meta charset="UTF-8">
<title>Moravel Aesthetic Doctor – Business Card</title>
<link href="https://fonts.googleapis.com/css2?family=Poppins:wght@400;500&display=swap" rel="stylesheet">
<style>
  :root {
    --backdrop: #1e1f21;
    --card: #ffffff;
    --accent: #4db8e8;
    --ink: #2b2b2b;
    --muted: #8f9196;
  }
  * { box-sizing: border-box; margin: 0; padding: 0; }
  html, body {
    width: 1200px; height: 1200px; overflow: hidden;
    background: var(--backdrop);
    font-family: "Poppins", sans-serif;
  }
  .stage {
    width: 1200px; height: 1200px;
    display: flex; flex-direction: column; align-items: center; justify-content: center;
    gap: 48px;
  }
  .card {
    position: relative;
    width: 900px; height: 514px;
    background: var(--card);
    box-shadow: 0 18px 40px rgba(0,0,0,.55);
  }
  .accent-bar {
    position: absolute; width: 18px; background: var(--accent);
  }
  .card-front .accent-bar.left { left: 0; top: 70px; height: 175px; }
  .card-front .accent-bar.right { right: 0; top: 190px; height: 190px; }
  .card-back .accent-bar.right { right: 0; top: 210px; height: 270px; }

  /* front */
  .brand {
    position: absolute; left: 0; right: 0; top: 165px;
    display: flex; align-items: center; justify-content: center; gap: 26px;
  }
  .brand-mark {
    width: 120px; height: 120px; border-radius: 50%;
    background: linear-gradient(135deg, #a6dcf3, #2f8fd0);
  }
  .brand-name {
    font-weight: 400; font-size: 40px; line-height: 1.15;
    color: var(--muted); letter-spacing: 2px; text-transform: uppercase;
  }
  .tagline {
    position: absolute; left: 0; right: 0; top: 335px;
    text-align: center; font-size: 20px; letter-spacing: 1.5px; color: var(--ink);
  }

  /* back */
  .person { position: absolute; left: 70px; top: 95px; right: 90px; }
  .person-name { font-weight: 500; font-size: 36px; color: var(--ink); }
  .person-name .post-nominals { font-weight: 400; font-size: 20px; color: var(--accent); margin-left: 6px; }
  .qualification { font-size: 22px; color: var(--accent); margin-top: 2px; }
  .divider { height: 2px; background: var(--accent); margin-top: 12px; width: 740px; }

  .contacts { position: absolute; left: 70px; top: 250px; list-style: none; }
  .contacts li {
    display: flex; align-items: center; gap: 16px;
    font-size: 22px; color: var(--ink); height: 36px;
  }
  .contact-icon { width: 26px; height: 26px; flex: none; }

  .social { position: absolute; left: 440px; top: 330px; display: flex; gap: 16px; }
  .social span { width: 32px; height: 32px; border-radius: 50%; background: var(--accent); }

  .services {
    position: absolute; left: 70px; top: 380px;
    font-size: 22px; line-height: 1.4; color: var(--ink);
  }
</style>
</head>
<body>
<main class="stage">

  <section class="card card-front">
    <div class="accent-bar left"></div>
    <div class="accent-bar right"></div>
    <div class="brand">
      <div class="brand-mark" role="img" aria-label="Brand emblem area"></div>
      <div class="brand-name">Moravel<br>Aesthetic Doctor</div>
    </div>
    <p class="tagline">Home and Spa Based Treatments</p>
  </section>

  <section class="card card-back">
    <div class="accent-bar right"></div>
    <div class="person">
      <h1 class="person-name">Dr Lena Varga<span class="post-nominals">MRCPCH MD</span></h1>
      <p class="qualification">Australasian Diploma of Aesthetic Medicine</p>
      <div class="divider"></div>
    </div>

    <ul class="contacts">
      <li>
        <svg class="contact-icon" viewBox="0 0 26 26" aria-hidden="true">
          <circle cx="13" cy="13" r="13" fill="#4db8e8"/>
          <path d="M8 9c0-1 1-2 5-2s5 1 5 2v1h-3V9h-4v1H8z M9 12h8l1 6H8z" fill="#fff"/>
        </svg>
        0800 555 018
      </li>
      <li>
        <svg class="contact-icon" viewBox="0 0 26 26" aria-hidden="true">
          <circle cx="13" cy="13" r="13" fill="#4db8e8"/>
          <rect x="7" y="9" width="12" height="8" fill="#fff"/>
          <path d="M7 9l6 5 6-5" fill="none" stroke="#4db8e8" stroke-width="1.2"/>
        </svg>
        lena@moravel.co.nz
      </li>
      <li>
        <svg class="contact-icon" viewBox="0 0 26 26" aria-hidden="true">
          <circle cx="13" cy="13" r="13" fill="#4db8e8"/>
          <g fill="none" stroke="#fff" stroke-width="1.2">
            <circle cx="13" cy="13" r="6"/>
            <ellipse cx="13" cy="13" rx="2.6" ry="6"/>
            <path d="M7 13h12"/>
          </g>
        </svg>
        www.moravel.co.nz
      </li>
    </ul>

    <div class="social" aria-hidden="true"><span></span><span></span></div>

    <p class="services">
      Dermal injectables - Plasma facials - Microneedling<br>
      Skin boosters - Excessive sweating<br>
      Home and Spa Based Treatments
    </p>
  </section>

</main>
</body>
</html>
```